Veltrano.co - Arctic Voyage Experts

We need a modern, visually striking business card for Veltrano.co, a company specialized in selling expedition cruises to the most remote regions on Earth, with a focus on the Arctic and Antarctica. The design should instantly communicate that the cardholder is an expert in polar travel. Use clean, premium aesthetics with cool tones like icy blue and white, possibly incorporating polar imagery (ice, glaciers, penguins, etc.)

Attached the logo

Contact Information for Business Card

Feels high-end and trustworthy.. Visually memorable — encourages people to keep it

Colors
0054AA
0677BA
7BADD7
CADEEF
E8F1F8

Requirements
Must have
• ice, glaciers, penguins, montains
Nice to have
• modern, transparente,

```html
<!DOCTYPE html>
<html lang="en">
<head>
<meta charset="UTF-8">
<title>Veltrano.co Business Card</title>
<link href="https://fonts.googleapis.com/css2?family=Poppins:wght@400;600;700&display=swap" rel="stylesheet">
<style>
  :root {
    --bg: #6b6b6b;
    --ink: #2f6db5;
    --deep: #0054AA;
    --mid: #0677BA;
    --sky: #7BADD7;
    --frost: #CADEEF;
    --snow: #E8F1F8;
    --white: #ffffff;
  }
  * { margin: 0; padding: 0; box-sizing: border-box; }
  html, body {
    width: 1093px; height: 1200px; overflow: hidden;
    background: var(--bg);
    font-family: "Poppins", sans-serif;
  }
  .stage { position: relative; width: 1093px; height: 1200px; }
  .card {
    position: absolute; left: 264px;
    width: 580px; height: 357px; overflow: hidden;
  }
  .card--front { top: 226px; }
  .card--back { top: 620px; }
  .card__scene {
    position: absolute; inset: 0;
    background:
      linear-gradient(160deg, rgba(123,173,215,0.9) 0%, rgba(202,222,239,0.6) 45%, rgba(123,173,215,0.7) 75%, rgba(232,241,248,0.9) 100%),
      linear-gradient(180deg, var(--sky) 0%, var(--frost) 55%, var(--snow) 100%);
  }
  .card__rings { position: absolute; inset: 0; }
  .card__content {
    position: absolute; left: 149px; top: 47px;
    width: 282px; height: 282px;
    display: flex; flex-direction: column; align-items: center; justify-content: center;
    text-align: center; color: var(--ink);
  }
  .card--front .card__content { padding-bottom: 14px; }
  .holder__name { font-weight: 600; font-size: 24px; line-height: 1.1; }
  .holder__role { font-size: 17px; line-height: 1.2; }
  .divider { width: 45px; height: 1px; background: var(--ink); margin: 9px 0 7px; }
  .contact__line { font-size: 17px; line-height: 21px; }
  .brand__name { font-weight: 700; font-size: 42px; line-height: 1; margin-top: 100px; }
  .brand__tagline { font-weight: 600; font-size: 14px; margin-top: 6px; }
</style>
</head>
<body>
<main class="stage">

  <section class="card card--front">
    <div class="card__scene" role="img" aria-label="Snowy alpine mountain valley under a pale blue sky"></div>
    <svg class="card__rings" width="580" height="357" viewBox="0 0 580 357" aria-hidden="true">
      <circle cx="290" cy="188" r="225" fill="rgba(255,255,255,0.12)"/>
      <circle cx="290" cy="188" r="195" fill="rgba(255,255,255,0.14)"/>
      <circle cx="290" cy="188" r="168" fill="rgba(255,255,255,0.18)"/>
      <circle cx="290" cy="188" r="141" fill="var(--white)"/>
    </svg>
    <div class="card__content">
      <h1 class="holder__name">Marcus Hale</h1>
      <p class="holder__role">Managing Director</p>
      <span class="divider"></span>
      <p class="contact__line">044-987 654 321</p>
      <p class="contact__line">hello@veltrano.co</p>
      <p class="contact__line">www.veltrano-trips.com</p>
      <span class="divider"></span>
      <p class="contact__line">87, Harbour Quay Road East</p>
      <p class="contact__line">20815,Norvale Isle</p>
    </div>
  </section>

  <section class="card card--back">
    <div class="card__scene" role="img" aria-label="Snowy alpine mountain valley under a pale blue sky"></div>
    <svg class="card__rings" width="580" height="357" viewBox="0 0 580 357" aria-hidden="true">
      <circle cx="290" cy="188" r="225" fill="rgba(255,255,255,0.12)"/>
      <circle cx="290" cy="188" r="195" fill="rgba(255,255,255,0.14)"/>
      <circle cx="290" cy="188" r="168" fill="rgba(255,255,255,0.18)"/>
      <circle cx="290" cy="188" r="141" fill="var(--white)"/>
    </svg>
    <div class="card__content">
      <p class="brand__name">Veltrano.co</p>
      <p class="brand__tagline">Arctic Voyage Experts</p>
    </div>
  </section>

</main>
</body>
</html>
```